Innovative Media Company needs Web Design

We need a web design for a new multimedia product that we are launching to potential partners and investors. The initial website we are looking to launch consists of three pages:
1.) A home/feature set page
2.) An account landing page
3.) An about us page
We would like the style of our website to be VERY similar to the following site: http://www.brintaro.com/tundra.
We have worked a bit on this project with a previous designer but were not happy with the results. As a guideline, you may refer to their previous work and the Tundra 88 website.
We realize this prize is a bit low for this project. However, there is a great opportunity for follow-on work. We are hoping to make a long-term business relationship with a high quality web-developer.
Attached are the product logo and our previous designer's work. Please let me know if you have any questions.
Thank you.
All,
Thanks for your submissions. Please note that rather than have headers that state "Enhanced TV Functionality" and "Seamless Device Integration", I would like to see all features (the six or seven boxes) in the same section. Also, please revise your designs to have the following statement below the picture that stretches across the screen and above the feature descriptions:
"Available via apps for the television and mobile devices,
naLix technology integrates numerous media components to provide users with
enhanced TV functionality and seamless device integration for an unparalleled
personalized viewing experience."
Thanks you.

```html
<!DOCTYPE html>
<html lang="en">
<head>
<meta charset="utf-8">
<title>naLix — Next Generation Television</title>
<link rel="stylesheet" href="https://fonts.googleapis.com/css2?family=Exo+2:wght@300;400&family=Ubuntu:wght@400&display=swap">
<style>
:root{
  --ink:#2a2a2a;
  --text:#333333;
  --muted:#555555;
  --header-top:#f6f6f6;
  --header-bottom:#e4e4e4;
  --rule:#b9b9b9;
  --hero:#151515;
  --hero-light:#2c2c2c;
  --white:#ffffff;
  --footer:#262626;
  --footer-light:#323232;
  --footer-text:#d6d6d6;
  --footer-line:#3d3d3d;
}
*{margin:0;padding:0;box-sizing:border-box}
html,body{width:735px;height:1200px;overflow:hidden;background:var(--white)}
body{position:relative;font-family:"Ubuntu",sans-serif;color:var(--text)}
.abs{position:absolute}
.display{font-family:"Exo 2",sans-serif;font-weight:300}

/* Header */
.site-header{left:0;top:0;width:735px;height:90px;border-top:3px solid #c8c8c8;
  background:linear-gradient(var(--header-top),var(--header-bottom))}
.brand{left:26px;top:28px;display:flex;align-items:center;gap:8px}
.brand-dot{width:30px;height:30px;border-radius:50%;background:var(--ink)}
.brand-name{font-family:"Exo 2",sans-serif;font-weight:400;font-size:36px;color:var(--ink);line-height:1}
.main-nav{right:0;top:47px;display:flex}
.main-nav a{font-family:"Exo 2",sans-serif;font-size:12px;color:var(--ink);text-decoration:none;
  padding:0 16px;border-left:1px solid #c6c6c6;line-height:20px}
.main-nav a:first-child{border-left:none}

/* Hero */
.hero{left:0;top:90px;width:735px;height:325px;
  background:radial-gradient(circle at 70% 40%,var(--hero-light),var(--hero) 75%)}
.hero-photo{left:0;top:90px;width:440px;height:325px;
  background:radial-gradient(ellipse at 48% 45%,#3a3f55 0%,#24242a 45%,rgba(21,21,21,0) 75%),
             radial-gradient(ellipse at 30% 85%,#c89474 0%,rgba(200,148,116,0) 40%)}
.hero-copy{left:452px;top:175px;color:var(--white)}
.hero-kicker{font-size:23px;line-height:26px}
.hero-title{font-size:35px;line-height:33px}
.hero-button{left:459px;top:280px;width:81px;height:25px;border-radius:3px;
  background:linear-gradient(#ffffff,#d9d9d9);font-family:"Exo 2",sans-serif;font-size:12px;
  color:var(--ink);display:flex;align-items:center;justify-content:center;gap:4px}
.hero-arrows{left:662px;top:380px}

/* Intro */
.intro-title{left:20px;top:438px;font-size:25px;color:var(--ink)}
.intro-text{left:22px;top:477px;width:680px;font-size:8.4px;line-height:13px}
.dotted{left:20px;width:689px;border-top:1px dotted #8a8a8a}

/* Features */
.feature{top:576px;width:215px}
.feature h2{font-family:"Exo 2",sans-serif;font-weight:400;font-size:17px;color:var(--ink);margin-bottom:9px}
.feature-image{height:120px;border-radius:2px}
.feature p{font-size:8.4px;line-height:13px;margin-top:15px}
.read-more{font-family:"Exo 2",sans-serif;font-size:11px;color:var(--muted);margin-top:10px;display:flex;align-items:center;gap:4px}
.col-divider{top:580px;width:1px;height:118px;background:#d2d2d2}

/* About */
.about-title{left:22px;top:855px;font-size:19px;color:var(--ink);font-weight:400}
.about-text{left:22px;top:884px;width:680px;font-size:8.4px;line-height:13px}
.about-text p+p{margin-top:13px}

/* Footer */
.site-footer{left:0;top:997px;width:735px;height:175px;
  background:linear-gradient(var(--footer-light),var(--footer));border-top:2px solid #454545}
.footer-title{left:26px;top:1015px;font-size:16px;color:#cfcfcf}
.link-col{top:1041px;list-style:none}
.link-col li{font-size:8.4px;color:var(--footer-text);height:20px;line-height:20px}
.link-col.lined li{border-bottom:1px solid var(--footer-line)}
.footer-mark{left:568px;top:1030px;display:flex;flex-direction:column;align-items:center;gap:8px}
.footer-mark-dot{width:44px;height:44px;border-radius:50%;background:#4a4a4a}
.footer-mark-name{font-family:"Exo 2",sans-serif;font-weight:400;font-size:34px;color:#4a4a4a}
.bottom-bar{left:0;top:1172px;width:735px;height:28px;background:#1c1c1c;border-top:1px solid #3a3a3a}
.copyright{left:20px;top:1180px;font-size:8px;color:#cfcfcf}
</style>
</head>
<body>

<header class="site-header abs"></header>
<div class="brand abs"><span class="brand-dot"></span><span class="brand-name">naLix</span></div>
<nav class="main-nav abs">
  <a href="#">Home</a><a href="#">Product info</a><a href="#">About Us</a><a href="#">Contact</a><a href="#">Help</a>
</nav>

<section class="hero abs"></section>
<div class="hero-photo abs" role="img" aria-label="Hands holding a tablet showing a media library of album covers"></div>
<div class="hero-copy abs display">
  <div class="hero-kicker">Step into the</div>
  <div class="hero-title">Next Generation<br>of television</div>
</div>
<div class="hero-button abs">learn more
  <svg width="6" height="9" viewBox="0 0 6 9"><path d="M1 1l3.5 3.5L1 8" fill="none" stroke="#2a2a2a" stroke-width="1.3"/></svg>
</div>
<svg class="hero-arrows abs" width="34" height="22" viewBox="0 0 34 22">
  <path d="M10 1L1 11l9 10" fill="none" stroke="#cfcfcf" stroke-width="1.3"/>
  <path d="M24 1l9 10-9 10" fill="none" stroke="#cfcfcf" stroke-width="1.3"/>
</svg>

<h1 class="intro-title abs display">Get the next generation television now !</h1>
<p class="intro-text abs">E-Commerce is a major progress in technology that has changed the way in which the customers now purchase information, products and the services. It's the new way of providing an opportunity to make your products and services available in the global market 24 hours a day through Internet&nbsp; Brightwave Studio is specialized in handling advanced web projects and the ongoing projects that require permanent maintenance and support .We like challenges and do complete these challenge with expertise we like solving questions that arises in such projects as these helps us to grow also.</p>

<div class="dotted abs" style="top:550px"></div>

<article class="feature abs" style="left:22px">
  <h2>TV Functionality</h2>
  <div class="feature-image" style="width:174px;background:linear-gradient(#6f93c4 0%,#a9c3dc 45%,#c7402c 70%,#3f6a28 100%)" role="img" aria-label="Flat screen television showing a field of tulips and a windmill"></div>
  <p>Brightwave Studio is specialized in handling advanced web projects and the ongoing projects that require permanent maintenance and support .We like challenges and do complete these challenge with expertise</p>
  <div class="read-more">READ MORE <svg width="5" height="8" viewBox="0 0 5 8"><path d="M1 1l3 3-3 3" fill="none" stroke="#555" stroke-width="1"/></svg></div>
</article>
<div class="col-divider abs" style="left:247px"></div>

<article class="feature abs" style="left:263px">
  <h2>Device Integration</h2>
  <div class="feature-image" style="width:150px;background:linear-gradient(135deg,#1d1d1d,#5d6b7e 55%,#222)" role="img" aria-label="Tablet and two smartphones showing a synced app"></div>
  <p>Brightwave Studio is specialized in handling advanced web projects and the ongoing projects that require permanent maintenance and support .We like challenges and do complete these challenge with expertise</p>
  <div class="read-more">READ MORE <svg width="5" height="8" viewBox="0 0 5 8"><path d="M1 1l3 3-3 3" fill="none" stroke="#555" stroke-width="1"/></svg></div>
</article>
<div class="col-divider abs" style="left:490px"></div>

<article class="feature abs" style="left:510px">
  <h2>Next Level product</h2>
  <div class="feature-image" style="width:185px;background:radial-gradient(ellipse at 45% 60%,#3e5f9a 0%,#25324a 40%,#ffffff 72%)" role="img" aria-label="Tablet lying flat with a stylus"></div>
  <p>Brightwave Studio is specialized in handling advanced web projects and the ongoing projects that require permanent maintenance and support .We like challenges and do complete these challenge with expertise</p>
  <div class="read-more">READ MORE <svg width="5" height="8" viewBox="0 0 5 8"><path d="M1 1l3 3-3 3" fill="none" stroke="#555" stroke-width="1"/></svg></div>
</article>

<div class="dotted abs" style="top:838px"></div>

<h2 class="about-title abs display">Little About our Company</h2>
<div class="about-text abs">
  <p>Static website are the which are usually been used and are benefited through the Professionals and Small Companies. The companies with fewer budgets can promote their products and services through the static website and gain a lot.</p>
  <p>To manage the static website HTML knowledge is the required. The simple website are also said as the static web as its embedded on a page.<br>Static website is a simple way to get your message out to the public. Static website are cheaper and also it needs less maintenance too. It's the simplest, cheapest and also the basic thing the search engine picks it up very easily. We at Brightwave provide you the best simple websites too with total work done as using all the best designing and all done so that you can achieve the goal of yours through our work done on your website.</p>
</div>

<footer class="site-footer abs"></footer>
<div class="footer-title abs display">Quick links</div>
<ul class="link-col abs" style="left:28px"><li>Home Page</li><li>About Our Company</li><li>Services Overview</li><li>Product List</li><li>Testimonials</li></ul>
<ul class="link-col abs" style="left:129px"><li>Recent Blog</li><li>Next Generation</li><li>Television</li><li>News &amp; Blog</li><li>FAQ</li></ul>
<ul class="link-col lined abs" style="left:220px;width:94px"><li>Product Goes here</li><li>IInd Product</li><li>IIIrd Product</li><li>More Products</li></ul>
<ul class="link-col lined abs" style="left:314px;width:108px"><li>Product Goes here</li><li>IInd Product</li><li>IIIrd Product</li><li>More Products</li></ul>
<ul class="link-col lined abs" style="left:422px;width:70px"><li>Product Goes here</li><li>IInd Product</li><li>IIIrd Product</li><li>More Products</li></ul>
<div class="footer-mark abs"><span class="footer-mark-dot"></span><span class="footer-mark-name">naLix</span></div>

<div class="bottom-bar abs"></div>
<div class="copyright abs">© 2012 Company Name &nbsp;|&nbsp; All right reserved</div>

</body>
</html>
```